MarbleTrove - New Website Design

Create a professional Vendora website for the hottest trend; a box of school supplies subscription box business called MarbleTrove. Vendora.com is an easy to use website builder.
Please see fizwickpod.com; plumfolly.com; tarrowmintloft.com; and nipcove.com for the concept I am after. The business has not been launched yet, I am currently in the pre-launch stage using a specialized landing page website, and so the time scale for developing my professional looking Vendora website is up to 1-2 weeks.
The webpage should have a fun feel and should match the style of the company logo at plumfolly.com. The pages to include are 'Home', 'About us' and 'Get Started'
Thank you and good luck!
1 page

```html
<!DOCTYPE html>
<html lang="en">
<head>
<meta charset="utf-8">
<title>MarbleTrove – School Supplies Box</title>
<link rel="stylesheet" href="https://fonts.googleapis.com/css2?family=Open+Sans:wght@400;600;700&family=Oleo+Script&display=swap">
<style>
:root{
  --pink:#ea1f6b;
  --blue:#14a8e6;
  --ink:#222;
  --text:#555;
  --muted:#888;
  --line:#e6e6e6;
  --soft:#f7f7f7;
  --dark:#1b1b1b;
  --darker:#0f0f0f;
}
*{box-sizing:border-box;margin:0;padding:0}
html,body{width:1200px;height:4543px;overflow:hidden}
body{font-family:"Open Sans",Arial,sans-serif;color:var(--text);background:#fff;position:relative}
.abs{position:absolute}
.script{font-family:"Oleo Script",Georgia,cursive}
svg{display:block}

/* top bar */
.topbar{top:0;left:0;width:1200px;height:39px;background:var(--ink);color:#ddd;font-size:11px;display:flex;align-items:center;padding:0 97px;gap:22px}
.topbar .right{margin-left:auto;display:flex;gap:22px;align-items:center}
.topbar .socials{display:flex;gap:6px}
.topbar .socials i{width:8px;height:8px;border-radius:50%;background:#ddd;display:block}
.flag{display:inline-block;width:14px;height:9px;background:linear-gradient(#c33 0 33%,#fff 33% 66%,#c33 66%);margin-right:6px;vertical-align:middle}

/* header */
.header{top:39px;left:0;width:1200px;height:123px;border-bottom:1px solid var(--line)}
.brand{display:flex;align-items:center;gap:14px}
.brand .mark{width:38px;height:38px;background:var(--blue);border-radius:4px}
.brand .name{font-family:"Oleo Script",Georgia,cursive;color:var(--pink);font-size:32px}
.header .brand{position:absolute;left:97px;top:40px}
.header .tools{position:absolute;right:97px;top:50px;display:flex;align-items:center;gap:22px;font-size:14px;color:#333}
.header .sep{width:1px;height:18px;background:#777}

.nav{top:162px;left:0;width:1200px;height:86px;border-bottom:1px solid var(--line);display:flex;align-items:center;padding-left:97px;gap:0;font-size:13px;color:#333}
.nav a{color:#333;text-decoration:none;margin-right:52px}
.nav a.dd::after{content:"";display:inline-block;width:4px;height:4px;border-right:1px solid #333;border-bottom:1px solid #333;transform:rotate(45deg);margin-left:8px;vertical-align:3px}

/* hero */
.hero{top:249px;left:0;width:1200px;height:459px;background:linear-gradient(100deg,#f3f0ec 0%,#e9e3db 45%,#d8cfc2 100%)}
.hero .photo{position:absolute;right:210px;top:20px;width:330px;height:420px;border-radius:40%;background:radial-gradient(ellipse at 50% 60%,#c6d98c 0%,#b7cc78 40%,rgba(183,204,120,0) 70%)}
.hero h1{position:absolute;left:97px;top:130px;font-family:"Oleo Script",Georgia,cursive;font-size:64px;color:#1c1c1c;font-weight:400}
.hero p{position:absolute;left:99px;top:227px;font-size:13px;color:#333}
.btn{display:inline-block;background:var(--blue);color:#fff;font-size:12px;text-transform:uppercase;padding:0 26px;line-height:38px}
.btn.pink{background:var(--pink)}
.hero .btn{position:absolute;left:99px;top:274px}
.dots{position:absolute;left:558px;top:407px;display:flex;gap:12px}
.dots i{width:12px;height:12px;border-radius:50%;border:2px solid #fff;display:block}
.dots i.on{background:var(--pink);border-color:var(--pink)}

/* categories */
.cats{top:782px;left:99px;width:1003px;display:flex;gap:12px}
.cat{width:242px}
.cat .img{height:228px}
.cat h3{margin-top:26px;font-size:13px;font-weight:600;color:#222;text-transform:uppercase}
.cat p{margin-top:14px;font-size:11.5px;line-height:24px;color:#777}
.rule{top:1202px;left:99px;width:1003px;height:1px;background:var(--line)}

.title{left:0;width:1200px;text-align:center;font-family:"Oleo Script",Georgia,cursive;font-size:30px;color:#1c1c1c}
.title::after{content:"";display:block;width:54px;height:3px;background:var(--pink);margin:14px auto 0}

/* featured */
.feature-img{top:1380px;left:99px;width:506px;height:528px;background:radial-gradient(circle at 55% 55%,#d9b58e 0%,#c49c72 22%,#cfe8f3 46%,#c4e4f1 100%)}
.grid{top:1380px;left:639px;width:463px;display:grid;grid-template-columns:repeat(3,143px);column-gap:17px;row-gap:118px}
.prod{width:143px;text-align:center;position:relative}
.prod .box{height:164px;border:1px solid var(--line);display:flex;align-items:center;justify-content:center}
.prod .box div{width:96px;height:104px;border-radius:8px}
.prod h4{margin-top:12px;font-size:14px;font-weight:400;color:#333}
.prod .price{margin-top:6px;font-size:14px;color:var(--pink);font-weight:600}
.stars{margin-top:6px;display:flex;justify-content:center;gap:3px}
.stars i{width:8px;height:8px;background:#ccc;display:block;clip-path:polygon(50% 0,61% 35%,98% 35%,68% 57%,79% 91%,50% 70%,21% 91%,32% 57%,2% 35%,39% 35%)}
.quick{position:absolute;left:0;top:26px;display:flex;flex-direction:column;gap:4px}
.quick i{width:20px;height:20px;background:var(--blue);display:block}

/* offers */
.offers{top:1984px;left:0;width:1200px;height:460px;display:grid;grid-template-columns:314px 286px 286px 314px}
.offer-pink{background:linear-gradient(160deg,#f25b8c,#e81f66);position:relative}
.offer-pink h2{position:absolute;left:97px;top:150px;font-family:"Oleo Script",Georgia,cursive;color:#fff;font-size:56px;line-height:62px;font-weight:400}
.offer-pink .btn{position:absolute;left:97px;top:277px;background:var(--blue)}
.offer-blue{background:linear-gradient(200deg,#5cc8f2,#1ba4e2);position:relative}
.offer-blue h2{position:absolute;left:76px;top:70px;font-family:"Oleo Script",Georgia,cursive;color:#fff;font-size:52px;line-height:64px;font-weight:400}
.offer-blue .btn{position:absolute;left:96px;top:343px}
.stack{display:grid;grid-template-rows:230px 230px}

/* latest */
.tabs{top:2607px;left:374px;width:452px;height:44px;display:flex;border:1px solid var(--line);font-size:12px;color:#555}
.tabs span{display:flex;align-items:center;justify-content:center;border-right:1px solid var(--line)}
.tabs span:last-child{border-right:0}
.tabs .on{background:var(--blue);color:#fff;font-weight:700}
.gallery{top:2697px;left:0;width:1200px;height:263px;display:grid;grid-template-columns:repeat(4,300px)}
.hover{position:relative;background:linear-gradient(160deg,#3aa7d9,#1670a6)}
.hover::before{content:"";position:absolute;inset:0;background:rgba(20,168,230,.55)}
.hover .ico{position:absolute;top:94px;left:110px;display:flex;gap:10px}
.hover .ico i{width:30px;height:30px;border:1px solid #fff;display:block}
.hover .cap{position:absolute;left:44px;top:155px;color:#fff;font-size:12px;text-transform:uppercase}

/* blog */
.post{top:3136px;width:493px;height:553px;border:1px solid var(--line)}
.post .img{height:315px}
.post .body{padding:34px 38px}
.post .date{color:var(--blue);font-size:13px;display:flex;align-items:center;gap:6px}
.post .meta{margin-top:14px;font-size:10.5px;color:#999}
.post h3{margin-top:22px;font-size:15px;font-weight:400;color:#333}
.post p{margin-top:14px;font-size:11.5px;line-height:24px;color:#888}
.post .more{margin-top:12px;display:inline-block;font-size:11px;color:var(--pink);text-decoration:underline}
.arrows{top:3728px;left:558px;display:flex;gap:6px}
.arrows span{width:36px;height:34px;background:var(--blue);display:flex;align-items:center;justify-content:center}

/* services */
.services{top:3834px;left:0;width:1200px;height:229px;background:var(--soft);display:grid;grid-template-columns:repeat(4,1fr);padding:60px 40px 0}
.svc{text-align:center;border-right:1px solid var(--line);height:100px}
.svc:last-child{border-right:0}
.svc svg{margin:0 auto}
.svc h4{margin-top:18px;font-size:16px;font-weight:400;color:#333}
.svc p{margin-top:8px;font-size:11.5px;color:#888}

/* footer */
.foot-left{top:4063px;left:0;width:537px;height:480px;background:var(--dark);color:#ddd}
.foot-right{top:4063px;left:537px;width:663px;height:480px;background:var(--darker);color:#ddd}
.foot-left .brand{position:absolute;left:97px;top:68px}
.foot-left .brand .name{color:#fff}
.foot-left .about{position:absolute;left:97px;top:165px;width:380px;font-size:11.5px;line-height:26px}
.contact{position:absolute;left:97px;font-size:11.5px;line-height:24px;display:flex;gap:18px;align-items:flex-start}
.cols{position:absolute;left:66px;top:60px;display:grid;grid-template-columns:200px 187px 150px}
.cols h5{font-size:15px;font-weight:600;color:#fff;text-transform:uppercase;margin-bottom:18px}
.cols li{list-style:none;font-size:11.5px;line-height:36px;display:flex;align-items:center;gap:16px}
.cols li::before{content:"";width:5px;height:5px;border-top:1.5px solid #ddd;border-right:1.5px solid #ddd;transform:rotate(45deg)}
.social{position:absolute;left:66px;top:328px;display:flex;gap:8px}
.social i{width:34px;height:34px;border:1.5px solid #ccc;border-radius:50%;display:block}
.cards{position:absolute;left:396px;top:340px;display:flex;gap:4px}
.cards i{width:28px;height:18px;border-radius:2px;display:block}
.copy{position:absolute;left:0;top:432px;width:663px;text-align:center;font-size:11px;color:#ccc}
</style>
</head>
<body>

<div class="abs topbar">
  <span><span class="flag"></span>USD</span>
  <span>(555) - 014 - 2290</span>
  <span>Mon - Sat : 9:00 am - 10:00 pm</span>
  <div class="right">
    <span>hello@marbletrove.com</span>
    <span class="socials"><i></i><i></i><i></i><i></i></span>
  </div>
</div>

<header class="abs header">
  <div class="brand"><span class="mark"></span><span class="name">MarbleTrove</span></div>
  <div class="tools">
    <svg width="16" height="16" viewBox="0 0 16 16"><circle cx="6.5" cy="6.5" r="5" fill="none" stroke="#333" stroke-width="2"/><path d="M10 10l5 5" stroke="#333" stroke-width="2.4"/></svg>
    <span class="sep"></span>
    <span style="display:flex;align-items:center;gap:8px"><svg width="18" height="16" viewBox="0 0 18 16"><path d="M0 1h3l2 9h10l2-7H5" fill="none" stroke="#333" stroke-width="2"/><circle cx="6" cy="14" r="1.6" fill="#333"/><circle cx="14" cy="14" r="1.6" fill="#333"/></svg>- 0 item</span>
    <span class="sep"></span>
    <svg width="18" height="14" viewBox="0 0 18 14"><path d="M0 1h18M0 7h18M0 13h18" stroke="#333" stroke-width="2.4"/></svg>
  </div>
</header>

<nav class="abs nav">
  <a>Home</a><a>About Us</a><a class="dd">Products</a><a>Shop</a><a class="dd">What's Inside</a><a class="dd">Pages</a><a>Log in</a>
</nav>

<section class="abs hero">
  <div class="photo" role="img" aria-label="Green pot filled with coloured pencils on a classroom desk"></div>
  <h1>MarbleTrove</h1>
  <p>Neque porro quisquam est qui dolorem ipsum quia dolor sit amet consecter</p>
  <a class="btn">Shop now</a>
  <div class="dots"><i class="on"></i><i></i><i></i><i></i></div>
</section>

<section class="abs cats">
  <article class="cat"><div class="img" role="img" aria-label="Pink coloured pencil tips" style="background:linear-gradient(135deg,#f47aa8,#e63a7d)"></div><h3>Vero eosaccusam</h3><p>Nam libero tempore, cum soluta nobis est eligendi optio cumque nihil impedit quo minus quod maxime..</p></article>
  <article class="cat"><div class="img" role="img" aria-label="Notebook, pencils and glasses on a desk" style="background:linear-gradient(135deg,#c99a6d,#e8dccb)"></div><h3>Nam libero tempore</h3><p>Nam libero tempore, cum soluta nobis est eligendi optio cumque nihil impedit quo minus quod maxime..</p></article>
  <article class="cat"><div class="img" role="img" aria-label="Box of pastel chalk sticks" style="background:linear-gradient(135deg,#4a4656,#8fb5c9)"></div><h3>Cum solutanobis est</h3><p>Nam libero tempore, cum soluta nobis est eligendi optio cumque nihil impedit quo minus quod maxime..</p></article>
  <article class="cat"><div class="img" role="img" aria-label="Pencil cup with coloured pencils" style="background:linear-gradient(135deg,#e9d6c0,#b46a3f)"></div><h3>Harum quidem rerum</h3><p>Nam libero tempore, cum soluta nobis est eligendi optio cumque nihil impedit quo minus quod maxime..</p></article>
</section>
<div class="abs rule"></div>

<h2 class="abs title" style="top:1262px">Featured Products</h2>
<div class="abs feature-img" role="img" aria-label="Cardboard box full of school supplies with a desk lamp and plant"></div>
<section class="abs grid">
  <div class="prod"><div class="quick"><i></i><i></i><i></i><i></i></div><div class="box"><div role="img" aria-label="Markers" style="background:linear-gradient(135deg,#f04a6a,#3b6dd6)"></div></div><h4>Aliquam quaera</h4><div class="price">$46.28</div><div class="stars"><i></i><i></i><i></i><i></i><i></i></div></div>
  <div class="prod"><div class="box"><div role="img" aria-label="Red pencil tin" style="background:#e3262f"></div></div><h4>Aliquam quaera</h4><div class="price">$46.28</div><div class="stars"><i></i><i></i><i></i><i></i><i></i></div></div>
  <div class="prod"><div class="box"><div role="img" aria-label="Stack of coloured crayons" style="background:linear-gradient(#d94a4a,#e0b340,#4a9a5c,#3c6bb5)"></div></div><h4>Aliquam quaera</h4><div class="price">$46.28</div><div class="stars"><i></i><i></i><i></i><i></i><i></i></div></div>
  <div class="prod"><div class="box"><div role="img" aria-label="Crayon box" style="background:linear-gradient(#f2c62b,#3e9a46)"></div></div><h4>Aliquam quaera</h4><div class="price">$46.28</div><div class="stars"><i></i><i></i><i></i><i></i><i></i></div></div>
  <div class="prod"><div class="box"><div role="img" aria-label="Pencil cup" style="background:linear-gradient(#e7505f,#3a3f68)"></div></div><h4>Aliquam quaera</h4><div class="price">$46.28</div><div class="stars"><i></i><i></i><i></i><i></i><i></i></div></div>
  <div class="prod"><div class="box"><div role="img" aria-label="Box of supplies" style="background:linear-gradient(#d8b68c,#c79b6b)"></div></div><h4>Aliquam quaera</h4><div class="price">$46.28</div><div class="stars"><i></i><i></i><i></i><i></i><i></i></div></div>
</section>

<section class="abs offers">
  <div class="offer-pink" role="img" aria-label="Pink pencil holder"><h2>50%<br>Offer</h2><a class="btn">Shop now</a></div>
  <div class="stack">
    <div role="img" aria-label="Rows of coloured pencils" style="background:linear-gradient(135deg,#3b7a3a,#c9812f,#b8322c)"></div>
    <div role="img" aria-label="Pencils in a green pot" style="background:linear-gradient(135deg,#efece6,#9fc166)"></div>
  </div>
  <div class="stack">
    <div role="img" aria-label="Child writing in a notebook" style="background:linear-gradient(135deg,#5a4a3f,#e8e5e0)"></div>
    <div role="img" aria-label="Donation box of school supplies" style="background:linear-gradient(135deg,#2e2e2e,#e0b45a)"></div>
  </div>
  <div class="offer-blue" role="img" aria-label="Blue pens"><h2>Special<br>Offer<br>For<br>You !</h2><a class="btn pink">Shop now</a></div>
</section>

<h2 class="abs title" style="top:2503px">Latest Products</h2>
<div class="abs tabs"><span class="on" style="width:64px">All</span><span style="width:128px">Best Sellers</span><span style="width:130px">Top Sellers</span><span style="width:130px">Accessories</span></div>
<section class="abs gallery">
  <div class="hover" role="img" aria-label="Blue coloured pencils"><div class="ico"><i></i><i></i></div><div class="cap">Quis nostrum exercitationem</div></div>
  <div role="img" aria-label="Watercolour paint palette" style="background:linear-gradient(135deg,#b0684a,#6a3d7a,#d34b3f)"></div>
  <div role="img" aria-label="Pastel chalks in a tray" style="background:linear-gradient(135deg,#3d3d3d,#8c8c8c,#c97b8b)"></div>
  <div role="img" aria-label="Pencil sharpener and shavings" style="background:linear-gradient(135deg,#ece8e6,#d7d2cf,#f0d040)"></div>
</section>

<h2 class="abs title" style="top:3022px">The Blog</h2>
<article class="abs post" style="left:97px"><div class="img" role="img" aria-label="Orange pencils in a blue cup" style="background:linear-gradient(135deg,#e8e6e2,#e0692f,#2f47a6)"></div><div class="body">
  <div class="date"><svg width="12" height="12" viewBox="0 0 12 12"><rect x="1" y="2" width="10" height="9" fill="none" stroke="#14a8e6" stroke-width="1.5"/><path d="M1 5h10" stroke="#14a8e6"/></svg>May 29,2017</div>
  <div class="meta">5 Comments &nbsp;|&nbsp; By Admin</div>
  <h3>Nemo enim ipsam voluptatem quia voluptas</h3>
  <p>Sed ut perspiciatis unde omnis iste natus error sit voluptatem accusantium doloremque laudantium, totam rem aperiam,</p>
  <a class="more">READ MORE</a></div></article>
<article class="abs post" style="left:609px"><div class="img" role="img" aria-label="Pastel chalk sticks on a wooden tray" style="background:linear-gradient(135deg,#c99bb0,#a57158,#ddd7cf)"></div><div class="body">
  <div class="date"><svg width="12" height="12" viewBox="0 0 12 12"><rect x="1" y="2" width="10" height="9" fill="none" stroke="#14a8e6" stroke-width="1.5"/><path d="M1 5h10" stroke="#14a8e6"/></svg>May 29,2017</div>
  <div class="meta">5 Comments &nbsp;|&nbsp; By Admin</div>
  <h3>Nemo enim ipsam voluptatem quia voluptas</h3>
  <p>Sed ut perspiciatis unde omnis iste natus error sit voluptatem accusantium doloremque laudantium, totam rem aperiam,</p>
  <a class="more">READ MORE</a></div></article>
<div class="abs arrows">
  <span><svg width="10" height="10" viewBox="0 0 10 10"><path d="M7 1L3 5l4 4" fill="none" stroke="#fff" stroke-width="2"/></svg></span>
  <span><svg width="10" height="10" viewBox="0 0 10 10"><path d="M3 1l4 4-4 4" fill="none" stroke="#fff" stroke-width="2"/></svg></span>
</div>

<section class="abs services">
  <div class="svc"><svg width="34" height="28" viewBox="0 0 34 28"><rect x="1" y="3" width="20" height="16" fill="#14a8e6"/><path d="M21 8h7l5 6v5H21z" fill="#14a8e6"/><circle cx="8" cy="23" r="4" fill="#14a8e6"/><circle cx="27" cy="23" r="4" fill="#14a8e6"/></svg><h4>Free Delivery</h4><p>Delivery within 5 days</p></div>
  <div class="svc"><svg width="30" height="30" viewBox="0 0 30 30"><circle cx="15" cy="15" r="12" fill="none" stroke="#14a8e6" stroke-width="3"/><path d="M15 8v8h6" fill="none" stroke="#14a8e6" stroke-width="3"/></svg><h4>24/7 Customer Support</h4><p>Call Toll Free @ (555) - 014 - 2290</p></div>
  <div class="svc"><svg width="30" height="28" viewBox="0 0 30 28"><path d="M14 2L2 14l12 12M2 14h27" fill="none" stroke="#14a8e6" stroke-width="5"/></svg><h4>Return of Goods</h4><p>No charge on Emi</p></div>
  <div class="svc"><svg width="32" height="30" viewBox="0 0 32 30"><path d="M16 1v16M9 11l7 7 7-7" fill="none" stroke="#14a8e6" stroke-width="4"/><rect x="1" y="21" width="30" height="8" fill="#14a8e6"/></svg><h4>Great Savings</h4><p>For Special Products</p></div>
</section>

<footer>
  <div class="abs foot-left">
    <div class="brand"><span class="mark"></span><span class="name">MarbleTrove</span></div>
    <p class="about">Nemo enim ipsam voluptatem quia voluptas sit aspernatur aut odit aut fugit, sed quia consequuntur magni dolores eos qui ratione voluptatem sequi nesciunt porro qui dolorem ipsum quia dolor sit amet, consectetursed quia non numquam..</p>
    <div class="contact" style="top:308px"><svg width="14" height="18" viewBox="0 0 14 18"><path d="M7 17S1 10 1 6.5a6 6 0 0112 0C13 10 7 17 7 17z" fill="none" stroke="#ddd" stroke-width="1.5"/><circle cx="7" cy="6.5" r="2" fill="#ddd"/></svg><span>12 Quillby Lane, Sit voluptatem dolore<br>laud rem aperiameaque ipsa.</span></div>
    <div class="contact" style="top:372px"><svg width="16" height="16" viewBox="0 0 16 16"><path d="M3 1l3 3-2 2c1 3 3 5 6 6l2-2 3 3-2 2C7 15 1 9 1 3z" fill="none" stroke="#ddd" stroke-width="1.3"/></svg><span>Phone: (555) - 014 - 2290</span></div>
    <div class="contact" style="top:408px"><svg width="16" height="12" viewBox="0 0 16 12"><rect x="1" y="1" width="14" height="10" fill="none" stroke="#ddd" stroke-width="1.3"/><path d="M1 1l7 6 7-6" fill="none" stroke="#ddd" stroke-width="1.3"/></svg><span>Email : hello@marbletrove.com</span></div>
  </div>
  <div class="abs foot-right">
    <div class="cols">
      <div><h5>My Account</h5><ul><li>Policies</li><li>Orders</li><li>Return</li><li>Bulk Discount</li><li>Quality</li></ul></div>
      <div><h5>Quick Links</h5><ul><li>Press</li><li>Wholesale</li><li>Policies</li><li>Employment</li><li>Size Chart</li></ul></div>
      <div><h5>Other Links</h5><ul><li>Request Quote</li><li>Information</li><li>Phone &amp; Mail</li><li>Privacy</li><li>Terms of Use</li></ul></div>
    </div>
    <div class="social"><i></i><i></i><i></i><i></i></div>
    <div class="cards"><i style="background:#e9edf2"></i><i style="background:#f0f0f0"></i><i style="background:#2a5bb8"></i><i style="background:#3ea0d8"></i><i style="background:#f3f3f3"></i></div>
    <p class="copy">© copyright 2017 MarbleTrove . All Rights Reserved</p>
  </div>
</footer>

</body>
</html>
```